Velmora Consulting Business

** Please add the content information from my old business card
1. I would like to see a two sided business card with both options with the 1st Option--Tallow Spire-new WHITE BACKGROUND LOGO
2 nd Option-Tallow Spire - new BLACK- Background Logo
3rd -Option a business card with my Photo on the card
Please add the new word to the card information:
EXECUTION
AS THE OWNER'S REP
WE AIM TO ACHIEVE YOUR
INFRASTRUCTURE VISION with
OUR SPECIALIZATION & EXECUTION in:

FUNDING Planning
BUSINESS Planning
INFRASTRUCTURE Planning
PROJECT Management
Since 2012
_____________________________________________________________________
I want to get spot uv raised printing. I was liking a a nice rich white linen paper stock with black writing & NOT A COLORED CARD other than a variety of white or black cards concept

```html
<!DOCTYPE html>
<html lang="en">
<head>
<meta charset="utf-8">
<title>Velmora Consulting – Business Card</title>
<link rel="stylesheet" href="https://fonts.googleapis.com/css2?family=Arimo:wght@400;700&display=swap">
<style>
  :root {
    --page-bg: #1c1c1d;
    --card-white: #f4f4f4;
    --card-dark: #2a2a2c;
    --ink: #1f1f20;
    --ink-soft: #333335;
    --accent-red: #e0203a;
    --text-light: #f2f2f2;
    --logo-faint: #3c3c3f;
  }
  * { box-sizing: border-box; margin: 0; padding: 0; }
  html, body {
    width: 1200px; height: 1059px; overflow: hidden;
    background: var(--page-bg);
    font-family: "Arimo", Arial, sans-serif;
  }
  .card {
    position: absolute;
    left: 255px;
    width: 690px;
    height: 392px;
    border-radius: 24px;
    overflow: hidden;
  }
  .card--front { top: 89px; background: var(--card-white); }
  .card--back { top: 548px; background: var(--card-dark); }

  /* Front */
  .brand { position: absolute; left: 83px; top: 196px; width: 200px; }
  .brand__name {
    display: flex; align-items: center; gap: 8px;
    font-size: 40px; font-weight: 700; color: var(--ink); line-height: 1;
    letter-spacing: -0.5px;
  }
  .brand__mark { width: 12px; height: 12px; background: var(--accent-red); }
  .brand__tag {
    margin-top: 10px;
    font-size: 12px; letter-spacing: 12.6px; color: var(--ink); white-space: nowrap;
  }
  .divider {
    position: absolute; left: 306px; top: 94px; width: 1px; height: 166px;
    background: var(--ink-soft);
  }
  .contact { position: absolute; left: 333px; top: 91px; color: var(--ink); }
  .contact__name { font-size: 24px; font-weight: 700; color: var(--accent-red); line-height: 1; }
  .contact__role { margin-top: 7px; font-size: 15px; line-height: 1; }
  .contact__list { list-style: none; margin-top: 22px; }
  .contact__item {
    display: flex; align-items: center; gap: 6px;
    font-size: 17px; height: 25.5px;
  }
  .contact__item svg { width: 13px; height: 13px; flex: none; }
  .contact__offices { margin-top: 12px; font-size: 17px; }
  .swoosh { position: absolute; left: 0; top: 0; width: 690px; height: 392px; }

  /* Back */
  .back-brand {
    position: absolute; left: 0; right: 0; top: 56px; text-align: center;
    color: var(--logo-faint);
  }
  .back-brand__name { font-size: 62px; font-weight: 700; line-height: 1; letter-spacing: -1px; }
  .back-brand__tag { margin-top: 8px; font-size: 18px; letter-spacing: 16px; padding-left: 16px; }
  .pitch {
    position: absolute; left: 0; right: 0; top: 163px; text-align: center;
    color: var(--text-light); font-size: 19px; line-height: 30.5px;
  }
  .pitch__lead { color: var(--accent-red); }
  .rule {
    position: absolute; left: 0; width: 100%; height: 1.5px; background: var(--accent-red);
  }
  .rule--top { top: 258px; }
  .rule--bottom { top: 354px; }
  .services {
    position: absolute; left: 0; right: 0; top: 271px; text-align: center;
    color: var(--text-light); font-size: 19px; line-height: 32px;
  }
  .services__sep { color: var(--accent-red); margin: 0 6px; }
  .since {
    position: absolute; left: 288px; top: 342px; width: 116px; height: 25px;
    border: 1.5px solid var(--accent-red); border-radius: 13px;
    background: var(--card-dark); color: var(--text-light);
    font-size: 19px; line-height: 22px; text-align: center;
  }
</style>
</head>
<body>
  <section class="card card--front">
    <svg class="swoosh" viewBox="0 0 690 392" aria-hidden="true">
      <path d="M0,303 C160,335 310,366 460,368 C570,369 640,360 690,353 L690,392 L0,392 Z" fill="#2a2a2c"/>
      <path d="M230,346 C360,364 520,366 690,337 L690,348 C530,368 370,368 230,346 Z" fill="#e0203a"/>
    </svg>

    <div class="brand">
      <div class="brand__name"><span>Velmora</span><span class="brand__mark"></span></div>
      <div class="brand__tag">CONSULTING</div>
    </div>

    <div class="divider"></div>

    <div class="contact">
      <h1 class="contact__name">Marisol Quenby-Dartt</h1>
      <p class="contact__role">CEO / LEAD PROJECT MANAGER</p>
      <ul class="contact__list">
        <li class="contact__item">
          <svg viewBox="0 0 14 14"><path d="M1,6 C1,2 13,2 13,6 L10,6 L10,4.5 L4,4.5 L4,6 Z M3,7 L11,7 L12,12 L2,12 Z" fill="#e0203a"/></svg>
          867.555.0142
        </li>
        <li class="contact__item">
          <svg viewBox="0 0 14 14"><path d="M1,4 L13,4 L13,12 L1,12 Z" fill="#e0203a"/><path d="M1,4 L7,9 L13,4" fill="none" stroke="#f4f4f4" stroke-width="1.2"/></svg>
          mara@velmora.ca
        </li>
        <li class="contact__item">
          <svg viewBox="0 0 14 14"><circle cx="7" cy="7" r="6" fill="#e0203a"/><path d="M1,7 H13 M7,1 C4,4 4,10 7,13 M7,1 C10,4 10,10 7,13" fill="none" stroke="#f4f4f4" stroke-width="0.9"/></svg>
          www.velmora.ca
        </li>
      </ul>
      <p class="contact__offices">Northreach NT • Elmbrook NB</p>
    </div>
  </section>

  <section class="card card--back">
    <div class="back-brand">
      <div class="back-brand__name">Velmora</div>
      <div class="back-brand__tag">CONSULTING</div>
    </div>

    <div class="pitch">
      <p class="pitch__lead">AS THE OWNER'S REP</p>
      <p>WE AIM TO ACHIEVE YOUR INFRASTRUCTURE VISION</p>
      <p>with OUR SPECIALIZATION &amp; EXECUTION in:</p>
    </div>

    <div class="rule rule--top"></div>

    <div class="services">
      <p>FUNDING Planning<span class="services__sep">|</span>BUSINESS Planning</p>
      <p>INFRASTRUCTURE Planning<span class="services__sep">|</span>PROJECT Management</p>
    </div>

    <div class="rule rule--bottom"></div>
    <div class="since">Since 2012</div>
  </section>
</body>
</html>
```